kv tempore
Zielgruppe
My service company has specialists in Sales, Marketing and Change Management. Our target group is the 1st and 2nd management level of enterprises, who want to align their strategy at new market situations or to change their distribution, communication or product concept.
We help our clients in defined time frames or projects not only in defining new strategies and concepts but also in implementation and measurements of the results.
Aufgabenstellung
I'm looking for a design of business cards and A4 letter paper. The company name is "kv tempore"; my name ist Konrad Velm...
So the name of my company stands for Management on time (kv tempore) and kv stands for my name (initials)
Logo see enclosed.

```html
<!DOCTYPE html>
<html lang="de">
<head>
<meta charset="utf-8">
<title>kv tempore – Geschäftsausstattung</title>
<link href="https://fonts.googleapis.com/css2?family=Arimo:wght@400;700&display=swap" rel="stylesheet">
<style>
:root{
  --navy:#13264f;
  --grey-strip:#5d5d66;
  --ink:#1b1b1b;
  --muted:#6f6f74;
  --faint:#efeff1;
  --stage:#e6e6ea;
  --paper:#ffffff;
  --card:#f7f7f5;
}
*{margin:0;padding:0;box-sizing:border-box}
html,body{width:1200px;height:1200px;overflow:hidden;background:var(--stage);font-family:"Arimo",Arial,sans-serif;color:var(--ink)}
.canvas{position:relative;width:1200px;height:1200px}

/* letterheads */
.letter{position:absolute;top:20px;width:560px;height:792px;background:var(--paper);overflow:hidden;box-shadow:0 2px 10px rgba(0,0,0,.25)}
.letter--classic{left:20px}
.letter--framed{left:620px}
.letter--framed .edge-left{position:absolute;left:0;top:0;bottom:0;width:11px;background:var(--grey-strip)}
.letter--framed .edge-right{position:absolute;right:0;top:0;bottom:0;width:8px;background:var(--navy)}
.watermark-disc{position:absolute;border-radius:50%;background:var(--faint)}
.letter--classic .watermark-disc{width:240px;height:240px;right:-50px;bottom:-140px}
.letter--framed .watermark-disc{width:270px;height:270px;left:20px;bottom:-70px}

.brand{position:absolute;display:flex;align-items:center;gap:8px;color:var(--navy);font-weight:400;letter-spacing:.5px}
.brand__dot{width:14px;height:14px;border-radius:50%;background:var(--navy)}
.letter .brand{top:78px;right:26px;font-size:24px}
.letter--framed .brand{right:34px}

.letter__content{position:absolute;left:81px;top:110px;width:410px;font-size:7.6px;line-height:11.7px}
.letter--framed .letter__content{left:81px}
.sender{margin-bottom:5px}
.recipient{margin-bottom:105px}
.letter__content p{margin-bottom:11.7px}
.closing{margin-top:22px}
.signature{margin-top:68px;font-size:9px;line-height:11px}

.footer-classic{position:absolute;left:27px;right:27px;top:732px;border-top:1px solid #8a8a8a;padding-top:10px;text-align:center;font-size:6.5px;line-height:13.5px;color:var(--muted)}
.footer-framed{position:absolute;left:240px;top:735px;display:flex;gap:20px;font-size:6.8px;line-height:8.6px;color:var(--ink)}
.footer-framed__rule{width:1px;height:45px;background:#555;margin-right:2px;margin-top:-4px}

/* business cards */
.card{position:absolute;width:268px;height:174px;background:var(--card);overflow:hidden;box-shadow:0 2px 8px rgba(0,0,0,.22)}
.card .brand{left:50%;top:50%;transform:translate(-50%,-50%);font-size:26px}
.card__disc{position:absolute;width:120px;height:120px;border-radius:50%;background:#e9e9eb;left:-20px;bottom:-40px}
.card__band{position:absolute;left:0;right:0;height:12px}
.card--front-a .card__band--navy{top:14px;background:var(--navy);right:70px}
.card--front-a .card__band--grey{top:14px;left:198px;background:var(--grey-strip)}
.card__role{position:absolute;font-size:7px;letter-spacing:.6px;color:var(--navy)}
.card__name{position:absolute;color:var(--navy);font-size:17px;letter-spacing:.3px}
.card__addr,.card__contact{position:absolute;font-size:7px;line-height:9px;color:var(--ink)}
.card--front-a .card__role{left:118px;top:44px}
.card--front-a .card__name{left:100px;top:54px}
.card--front-a .card__addr{left:190px;top:82px;color:var(--navy)}
.card--front-a .card__contact{left:150px;top:108px}

.card--front-b .card__band--navy{bottom:12px;height:9px;background:var(--navy);left:0;right:80px}
.card--front-b .card__band--grey{bottom:12px;height:9px;left:188px;background:var(--grey-strip)}
.card--front-b .card__rule{position:absolute;left:132px;top:34px;width:1px;height:100px;background:#555}
.card--front-b .card__role{left:24px;top:70px;font-size:8px;letter-spacing:0}
.card--front-b .card__name{left:24px;top:81px;font-size:12px}
.card--front-b .card__addr{left:24px;top:100px;color:var(--navy)}
.card--front-b .card__contact{left:144px;top:66px}
</style>
</head>
<body>
<div class="canvas">

  <!-- Letterhead, classic -->
  <section class="letter letter--classic">
    <div class="watermark-disc"></div>
    <div class="brand"><span class="brand__dot"></span>kv tempore</div>
    <div class="letter__content">
      <div class="sender">Konrad Velm • Adresse 1 • Adresse 2</div>
      <div class="recipient">Max Mustermann<br>Straße<br>Ort</div>
      <p>Sehr geehrter Herr,</p>
      <p>Esse ut ex. Sed esse mollit quis laboris in pariatur, anim ut aliquip ullamco voluptate. Ex consectetur culpa in eu, proident aliqua mollit sint reprehenderit?</p>
      <p>Incididunt ut in dolore reprehenderit aliqua ad, mollit anim fugiat ea. Enim consequat ad, ipsum ad sint culpa amet consectetur, sed cupidatat. Sit commodo ut. Non, nisi excepteur, fugiat voluptate ullamco eu labore: Pariatur sint laboris. Ipsum ea culpa qui nisi id exercitation, voluptate sit qui esse. Nisi, sunt ipsum occaecat commodo ut, magna veniam sed sit. Nisi officia minim reprehenderit dolore exercitation in fugiat, pariatur do reprehenderit dolore? Dolore, nostrud dolor velit.</p>
      <p>Aute aliqua, sed nostrud ut in ex nulla id ut non mollit aute voluptate. Occaecat anim ea nostrud et dolor est fugiat tempor excepteur. Amet, esse culpa commodo proident ut commodo do aute.<br>Qui sed adipisicing voluptate est. Fugiat sint veniam in duis non deserunt sint commodo. Occaecat dolore magna ea mollit, enim dolor exercitation dolore sunt magna aute lorem ea ad exercitation?</p>
      <p>Consectetur id ea proident. Dolore sunt velit et reprehenderit aliqua eiusmod. Exercitation eu laboris ex occaecat deserunt dolore et excepteur sint in dolore nostrud laboris dolore culpa quis cupidatat. Ea cillum et. In, consectetur amet.</p>
      <p>In elit ullamco culpa, enim reprehenderit est dolore magna, ad lorem. Ipsum ea, minim mollit sit minim. Sed voluptate velit dolor in magna non aliqua cillum in officia in excepteur. Officia veniam ut, pariatur ad veniam reprehenderit ex sint consequat magna. Amet sunt, duis velit do qui culpa, adipisicing sint mollit officia in culpa aliqua. Lorem, aliqua non labore est enim. Ad officia commodo do eu consequat. Sunt in, eu cupidatat, qui aute proident, adipisicing fugiat dolore velit ut in sint eiusmod commodo laboris do.</p>
      <p class="closing">Mit freundlichen Grüßen</p>
      <div class="signature">Konrad Velm<br>Geschäftsführer</div>
    </div>
    <footer class="footer-classic">
      Konrad Velm • Adresse 1 • Adresse 2<br>
      Tel: +49 (0) 000000000 • Fax: +49 (0) 11111 • E-mail: info@xxxx.de • Web: www.xxxxxxx.de<br>
      Bankverbindung: xxxxxxxxxx • IBAN: xxxxxxxxxxxxxx • BIC: xxxxxxxxxxxxxxxxxx
    </footer>
  </section>

  <!-- Letterhead, framed -->
  <section class="letter letter--framed">
    <div class="edge-left"></div>
    <div class="edge-right"></div>
    <div class="watermark-disc"></div>
    <div class="brand"><span class="brand__dot"></span>kv tempore</div>
    <div class="letter__content">
      <div class="sender">Konrad Velm • Adresse 1 • Adresse 2</div>
      <div class="recipient">Max Mustermann<br>Straße<br>Ort</div>
      <p>Sehr geehrter Herr,</p>
      <p>Esse ut ex. Sed esse mollit quis laboris in pariatur, anim ut aliquip ullamco voluptate. Ex consectetur culpa in eu, proident aliqua mollit sint reprehenderit?</p>
      <p>Incididunt ut in dolore reprehenderit aliqua ad, mollit anim fugiat ea. Enim consequat ad, ipsum ad sint culpa amet consectetur, sed cupidatat. Sit commodo ut. Non, nisi excepteur, fugiat voluptate ullamco eu labore: Pariatur sint laboris. Ipsum ea culpa qui nisi id exercitation, voluptate sit qui esse. Nisi, sunt ipsum occaecat commodo ut, magna veniam sed sit. Nisi officia minim reprehenderit dolore exercitation in fugiat, pariatur do reprehenderit dolore? Dolore, nostrud dolor velit.</p>
      <p>Aute aliqua, sed nostrud ut in ex nulla id ut non mollit aute voluptate. Occaecat anim ea nostrud et dolor est fugiat tempor excepteur. Amet, esse culpa commodo proident ut commodo do aute.<br>Qui sed adipisicing voluptate est. Fugiat sint veniam in duis non deserunt sint commodo: Occaecat dolore magna ea mollit, enim dolor exercitation dolore sunt magna aute lorem ea ad exercitation?</p>
      <p>Consectetur id ea proident. Dolore sunt velit et reprehenderit aliqua eiusmod. Exercitation eu laboris ex occaecat deserunt dolore et excepteur sint in dolore nostrud laboris dolore culpa quis cupidatat. Ea cillum et. In, consectetur amet.</p>
      <p>In elit ullamco culpa, enim reprehenderit est dolore magna, ad lorem. Ipsum ea, minim mollit sit minim. Sed voluptate velit dolor in magna non aliqua cillum in officia in excepteur. Officia veniam ut, pariatur ad veniam reprehenderit ex sint consequat magna. Amet sunt, duis velit do qui culpa, adipisicing sint mollit officia in culpa aliqua. Lorem, aliqua non labore est enim. Ad officia commodo do eu consequat. Sunt in, eu cupidatat, qui aute proident, adipisicing fugiat dolore velit ut in sint eiusmod commodo laboris do.</p>
      <p class="closing">Mit freundlichen Grüßen</p>
      <div class="signature">Konrad Velm<br>Geschäftsführer</div>
    </div>
    <footer class="footer-framed">
      <div class="footer-framed__rule"></div>
      <div>Konrad Velm<br>Adresse 1<br>Adresse 2</div>
      <div>Tel: +49 (0) 000000000<br>Fax: +49 (0) 11111<br>E-mail: info@xxxxx.de<br>Web: www.xxxxxx.de</div>
      <div>Bankverbindung: xxxxxxxxxx<br>IBAN: xxxxxxxxxxxxxx<br>BIC: xxxxxxxxxxxxxxxxx</div>
    </footer>
  </section>

  <!-- Business cards, variant A -->
  <article class="card card--back" style="left:20px;top:880px">
    <div class="brand"><span class="brand__dot"></span>kv tempore</div>
  </article>
  <article class="card card--front-a" style="left:312px;top:880px">
    <div class="card__disc"></div>
    <div class="card__band card__band--navy"></div>
    <div class="card__band card__band--grey"></div>
    <div class="card__role">DIENSTLEISTUNGEN</div>
    <div class="card__name">KONRAD VELM</div>
    <div class="card__addr">Adresse 1<br>Adresse 2</div>
    <div class="card__contact">Tel. 01234 000000<br>Fax. 01234 000000<br>e: info@xxxxxxx.de<br>w: www.xxxxxx.de</div>
  </article>

  <!-- Business cards, variant B -->
  <article class="card card--back" style="left:620px;top:880px">
    <div class="brand"><span class="brand__dot"></span>kv tempore</div>
  </article>
  <article class="card card--front-b" style="left:912px;top:880px">
    <div class="card__band card__band--navy"></div>
    <div class="card__band card__band--grey"></div>
    <div class="card__rule"></div>
    <div class="card__role">Dienstleistungen</div>
    <div class="card__name">Konrad Velm</div>
    <div class="card__addr">Adresse 1<br>Adresse 2</div>
    <div class="card__contact"><b>Tel.</b> +49 (0) 0000000000<br><b>Fax</b> +49 (0) 0000000000<br><b>Email:</b> info@name.de<br><b>Web:</b> www.name.de</div>
  </article>

</div>
</body>
</html>
```